Business card for medical clinic

I need an upmarket, modern medical/health business card for my clinic

Contact Information for Business Card

name, address, email, qr code

```html
<!DOCTYPE html>
<html lang="en">
<head>
<meta charset="utf-8">
<title>Corvale Health Partners – Business Card</title>
<link rel="stylesheet" href="https://fonts.googleapis.com/css2?family=Poppins:wght@400;500;600&display=swap">
<style>
  :root {
    --stage: #222222;
    --card-white: #ffffff;
    --card-dark: #1e2027;
    --navy: #1b2a4a;
    --sky: #1fa3e0;
    --sky-light: #2bb2ea;
    --ink: #1a1a1a;
    --on-dark: #f2f2f2;
  }
  * { box-sizing: border-box; margin: 0; padding: 0; }
  html, body {
    width: 1200px; height: 780px; overflow: hidden;
    background: var(--stage);
    font-family: "Poppins", sans-serif;
  }
  .stage {
    width: 1200px; height: 780px;
    display: flex; align-items: center; justify-content: center; gap: 40px;
  }
  .card {
    position: relative;
    width: 540px; height: 309px;
    overflow: hidden;
    box-shadow: 0 10px 30px rgba(0,0,0,.45);
  }
  /* front */
  .card-front { background: var(--card-white); }
  .brand {
    position: absolute; left: 34px; top: 58px;
    display: flex; align-items: center; gap: 10px;
  }
  .brand-dot {
    width: 30px; height: 30px; border-radius: 50%;
    background: var(--sky);
    flex: none;
  }
  .brand-name {
    font-weight: 600; font-size: 17px; line-height: 1.25;
    color: var(--navy); letter-spacing: .08em; text-transform: uppercase;
  }
  .divider {
    position: absolute; left: 250px; top: 40px;
    width: 1px; height: 190px; background: var(--navy);
  }
  .person {
    position: absolute; left: 276px; top: 62px;
  }
  .person-name {
    font-size: 27px; line-height: 1.1; color: var(--sky-light); font-weight: 400;
  }
  .person-name .given { font-weight: 600; color: var(--sky); }
  .person-title {
    font-size: 12px; font-weight: 500; color: var(--ink); margin-top: 2px;
  }
  .contacts { list-style: none; margin-top: 16px; }
  .contacts li {
    display: flex; align-items: center; gap: 8px;
    font-size: 12.5px; color: var(--ink); line-height: 1.9;
  }
  .contacts svg { width: 13px; height: 13px; flex: none; }
  .address-band {
    position: absolute; left: 0; right: 0; bottom: 0; height: 34px;
    background: linear-gradient(90deg, var(--sky) 0%, #1d6ea8 35%, var(--navy) 70%, var(--navy) 82%, var(--sky) 100%);
    display: flex; align-items: center; padding-left: 30px;
    color: #ffffff; font-size: 12px; letter-spacing: .01em;
  }
  /* back */
  .card-back { background: var(--card-dark); }
  .back-brand {
    position: absolute; right: 40px; bottom: 46px;
    display: flex; align-items: center; gap: 10px;
  }
  .back-brand .brand-name { color: var(--on-dark); font-size: 16px; }
</style>
</head>
<body>
<main class="stage">
  <section class="card card-front" aria-label="Card front">
    <div class="brand">
      <span class="brand-dot"></span>
      <span class="brand-name">Corvale Health<br>Partners</span>
    </div>
    <div class="divider"></div>
    <div class="person">
      <h1 class="person-name"><span class="given">Marta</span> Keller</h1>
      <p class="person-title">Founder &amp; CEO</p>
      <ul class="contacts">
        <li>
          <svg viewBox="0 0 24 24" fill="var(--sky)"><path d="M6.6 10.8a15.1 15.1 0 0 0 6.6 6.6l2.2-2.2a1 1 0 0 1 1-.25 11.4 11.4 0 0 0 3.6.57 1 1 0 0 1 1 1V20a1 1 0 0 1-1 1A17 17 0 0 1 3 4a1 1 0 0 1 1-1h3.5a1 1 0 0 1 1 1c0 1.25.2 2.45.57 3.57a1 1 0 0 1-.25 1z"/></svg>
          (555) 014-2290
        </li>
        <li>
          <svg viewBox="0 0 24 24" fill="none" stroke="var(--sky)" stroke-width="2.2"><rect x="3" y="5" width="18" height="14" rx="2"/><path d="M3 7l9 6 9-6"/></svg>
          info@corvalehealth.com
        </li>
        <li>
          <svg viewBox="0 0 24 24" fill="none" stroke="var(--sky)" stroke-width="2"><circle cx="12" cy="12" r="9"/><path d="M3 12h18M12 3c3 3.2 3 14.8 0 18M12 3c-3 3.2-3 14.8 0 18"/></svg>
          www.corvalehealth.com
        </li>
      </ul>
    </div>
    <div class="address-band">418 Linden Ave. Suite 300 Brookdale, TX 75550</div>
  </section>

  <section class="card card-back" aria-label="Card back">
    <div class="back-brand">
      <span class="brand-name">Corvale Health<br>Partners</span>
    </div>
  </section>
</main>
</body>
</html>
```